Become a Mentor - For Musicians, Artists, Producers and Teachers

Here is the full creative brief:

https://files.quorvant.com/sheets/d/7kTbWmQa2_pLRz9XcN4eHs8JuYd3FoVgA6iBnCqE/view?mode=shared

Here is the background image file: https://www.stashvel.com/sh/48kdmwtnb7yrs2p/AAZm3kLPQwTx8VnHRe4jBcDu?dl=0

LOGO:
https://www.stashvel.com/sh/k382fubotn7wq6/AAJhT5LsRy2D-mKzPX9CvGhNb?dl=0

```html
<!DOCTYPE html>
<html lang="en">
<head>
<meta charset="utf-8">
<title>Become a Mentor – Poster Options</title>
<link rel="stylesheet" href="https://fonts.googleapis.com/css2?family=Montserrat:wght@300;400;500;600;700;800&family=Oswald:wght@300;400;500;600&display=swap">
<style>
  :root {
    --backdrop: #a9a9a9;
    --poster-black: #050508;
    --career-pink: #f2647c;
    --accent-pink: #ff3d7f;
    --accent-blue: #3a4dff;
    --band-blue: #1532c8;
    --white: #ffffff;
    --photo-deep: #1a0f3a;
    --photo-violet: #7a3fa8;
    --photo-magenta: #c84a9a;
    --photo-blue: #2b5fd8;
  }
  * { box-sizing: border-box; margin: 0; padding: 0; }
  html, body { width: 1200px; height: 501px; overflow: hidden; }
  body { background: var(--backdrop); font-family: "Montserrat", sans-serif; position: relative; }

  .poster {
    position: absolute; top: 42px; width: 308px; height: 436px;
    background: var(--poster-black); overflow: hidden; color: var(--white);
  }
  .poster--one { left: 49px; }
  .poster--two { left: 455px; }
  .poster--three { left: 861px; }

  .poster__photo {
    position: absolute; left: 0; top: 100px; width: 308px; height: 232px;
    background:
      radial-gradient(ellipse at 60% 35%, var(--photo-magenta) 0%, transparent 55%),
      radial-gradient(ellipse at 20% 60%, var(--photo-blue) 0%, transparent 50%),
      linear-gradient(180deg, var(--photo-deep) 0%, var(--photo-violet) 45%, #2a1c2a 75%, var(--poster-black) 100%);
  }

  .poster__band {
    position: absolute; left: 0; top: 332px; width: 308px; height: 40px;
    background: linear-gradient(90deg, rgba(21,50,200,.55) 0%, rgba(5,5,8,0) 25%, rgba(5,5,8,0) 75%, rgba(21,50,200,.55) 100%);
  }

  .poster__kicker {
    position: absolute; top: 12px; left: 0; width: 100%; text-align: center;
    color: var(--career-pink); font-size: 16px; letter-spacing: 4.6px; line-height: 18px;
  }
  .poster__lead {
    position: absolute; top: 40px; left: 0; width: 100%; text-align: center;
    font-size: 14px; letter-spacing: 6px; line-height: 16px; font-weight: 400;
  }
  .poster__headline {
    position: absolute; left: 0; width: 100%; text-align: center;
    font-weight: 600; color: var(--white); white-space: nowrap;
    text-shadow: 0 0 3px rgba(0,0,0,.6);
  }
  .poster__headline--mentor { top: 60px; font-size: 54px; line-height: 52px; letter-spacing: 0; }
  .poster__headline--today { top: 108px; font-size: 68px; line-height: 68px; letter-spacing: -1px; }

  .poster__copy {
    position: absolute; top: 340px; left: 0; width: 100%; text-align: center;
    font-size: 8.6px; line-height: 12px; font-weight: 400; white-space: nowrap;
  }
  .copy__pink { color: var(--accent-pink); font-weight: 500; }
  .copy__blue { color: var(--accent-blue); font-weight: 500; }

  .poster__apply {
    position: absolute; top: 385px; left: 15px; height: 12px; padding: 0 10px 0 5px;
    background: var(--band-blue); font-size: 8.5px; line-height: 12px; font-weight: 700;
    clip-path: polygon(0 0, 100% 0, 92% 100%, 0 100%);
  }
  .poster__phone {
    position: absolute; top: 398px; left: 16px; font-size: 17px; line-height: 20px; font-weight: 800; white-space: nowrap;
  }
  .poster__web {
    position: absolute; top: 419px; left: 17px; font-size: 8px; line-height: 10px;
    color: var(--accent-pink); font-weight: 500; white-space: nowrap;
  }

  .poster__brand {
    position: absolute; top: 394px; left: 212px; width: 92px; text-align: center;
    font-size: 6.5px; line-height: 9px; font-weight: 700; letter-spacing: .5px; color: var(--white);
    white-space: nowrap;
  }
  .brand__dot {
    display: block; width: 12px; height: 12px; border-radius: 50%;
    background: var(--accent-blue); margin: 0 auto 3px;
  }

  .poster--one .poster__kicker { font-weight: 800; }

  .poster--two .poster__kicker { font-weight: 300; letter-spacing: 5px; }
  .poster--two .poster__lead { font-weight: 300; }
  .poster--two .poster__copy { font-weight: 300; }

  .poster--three .poster__kicker,
  .poster--three .poster__lead,
  .poster--three .poster__copy,
  .poster--three .poster__apply,
  .poster--three .poster__phone,
  .poster--three .poster__web { font-family: "Oswald", sans-serif; }
  .poster--three .poster__kicker { font-weight: 400; font-size: 17px; letter-spacing: 4px; }
  .poster--three .poster__lead { color: var(--accent-blue); font-weight: 600; font-size: 15px; letter-spacing: 5px; }
  .poster--three .poster__copy { font-size: 9.6px; line-height: 13px; font-weight: 300; }
  .poster--three .copy__pink,
  .poster--three .copy__blue { font-weight: 400; }
  .poster--three .poster__phone { font-weight: 500; font-size: 21px; top: 394px; letter-spacing: .3px; }
  .poster--three .poster__apply { font-weight: 500; top: 381px; }
  .poster--three .poster__web { top: 420px; letter-spacing: .5px; font-weight: 400; }
</style>
</head>
<body>

<section class="poster poster--one">
  <div class="poster__photo" role="img" aria-label="Photo of two young musicians talking in a recording studio with a mixing desk and colourful light equaliser background"></div>
  <div class="poster__band"></div>
  <p class="poster__kicker">START YOUR CAREER</p>
  <p class="poster__lead">BECOME A</p>
  <h1 class="poster__headline poster__headline--mentor">MENTOR</h1>
  <h1 class="poster__headline poster__headline--today">TODAY</h1>
  <p class="poster__copy">Turn your skills and passion for <span class="copy__pink">MUSIC INTO A CAREER</span><br>Designed for <span class="copy__blue">MUSICIANS, ARTISTS, PRODUCERS &amp; TEACHERS</span></p>
  <p class="poster__apply">APPLY NOW</p>
  <p class="poster__phone">CALL 1300 482 615</p>
  <p class="poster__web">www.meridianacademyofsound.com.au</p>
  <p class="poster__brand"><span class="brand__dot"></span>MERIDIAN<br>ACADEMY OF SOUND</p>
</section>

<section class="poster poster--two">
  <div class="poster__photo" role="img" aria-label="Photo of two young musicians talking in a recording studio with a mixing desk and colourful light equaliser background"></div>
  <div class="poster__band"></div>
  <p class="poster__kicker">START YOUR CAREER</p>
  <p class="poster__lead">BECOME A</p>
  <h1 class="poster__headline poster__headline--mentor">MENTOR</h1>
  <h1 class="poster__headline poster__headline--today">TODAY</h1>
  <p class="poster__copy">Turn your skills and passion for <span class="copy__pink">MUSIC INTO A CAREER</span><br>Designed for <span class="copy__blue">MUSICIANS, ARTISTS, PRODUCERS &amp; TEACHERS</span></p>
  <p class="poster__apply">APPLY NOW</p>
  <p class="poster__phone">CALL 1300 482 615</p>
  <p class="poster__web">www.meridianacademyofsound.com.au</p>
  <p class="poster__brand"><span class="brand__dot"></span>MERIDIAN<br>ACADEMY OF SOUND</p>
</section>

<section class="poster poster--three">
  <div class="poster__photo" role="img" aria-label="Photo of two young musicians talking in a recording studio with a mixing desk and colourful light equaliser background"></div>
  <div class="poster__band"></div>
  <p class="poster__kicker">START YOUR CAREER</p>
  <p class="poster__lead">BECOME A</p>
  <h1 class="poster__headline poster__headline--mentor">MENTOR</h1>
  <h1 class="poster__headline poster__headline--today">TODAY</h1>
  <p class="poster__copy">Turn your skills and passion for <span class="copy__pink">MUSIC INTO A CAREER</span><br>Designed for <span class="copy__blue">MUSICIANS, ARTISTS, PRODUCERS &amp; TEACHERS</span></p>
  <p class="poster__apply">APPLY NOW</p>
  <p class="poster__phone">CALL 1300 482 615</p>
  <p class="poster__web">www.meridianacademyofsound.com.au</p>
  <p class="poster__brand"><span class="brand__dot"></span>MERIDIAN<br>ACADEMY OF SOUND</p>
</section>

</body>
</html>
```